Postcard design to acquire new clients for my Property Management Company

I'm looking for a postcard design that I can send to prospective clients detailing information about my company and services.
Postcard should be eye catching and contain information from www.bramblecrestpm.com. I've provided a few screen shots for the most important information and my logo.
Target Market(s)
Real Estate
Industry/Entity Type
Real Estate
Font styles to use
Sans Serif
Requirements
Must have
- Must be eye catching!! this will be a direct mail piece - I'd like for the card to be read and not tossed in the trash immediately.
Design que from the logo.
A place to write / print the receipts name and address.
our physical address - 2387 Hollow Pine Road, Lubbock, TX 79852.
Should not have
- the contact information on the business card is not accurate - please use info from website.

```html
<!DOCTYPE html>
<html lang="en">
<head>
<meta charset="utf-8">
<title>Bramblecrest Property Management – Postcard</title>
<link href="https://fonts.googleapis.com/css2?family=Montserrat:wght@300;400;500;700;800&display=swap" rel="stylesheet">
<style>
  :root {
    --navy: #0b4a85;
    --navy-deep: #123f6e;
    --grey: #a3a3a3;
    --grey-text: #7c7c7c;
    --white: #ffffff;
    --stage: #e9ecf0;
    --ink: #4a4a4a;
  }
  * { margin: 0; padding: 0; box-sizing: border-box; }
  html, body { width: 933px; height: 1200px; overflow: hidden; }
  body { background: var(--stage); font-family: 'Montserrat', sans-serif; position: relative; }

  .postcard { position: absolute; left: 80px; width: 758px; background: var(--white); overflow: hidden; box-shadow: 0 6px 18px rgba(0,0,0,.18); }
  .postcard--front { top: 75px; height: 505px; }
  .postcard--back { top: 626px; height: 507px; }
  .postcard__shapes { position: absolute; inset: 0; width: 100%; height: 100%; }
  .abs { position: absolute; }

  .brand { color: var(--navy); font-weight: 500; text-align: center; line-height: 1.2; white-space: nowrap; width: 256px; }
  .brand__name { display: block; font-size: 24px; letter-spacing: 3px; }
  .brand__tag { display: block; font-size: 12.5px; letter-spacing: 2.6px; }

  .front__brand { left: 470px; top: 96px; }
  .front__headline { right: 35px; top: 203px; text-align: right; color: var(--white); font-weight: 800; font-size: 28px; line-height: 1.2; }
  .services__title { left: 36px; top: 302px; color: var(--navy); font-weight: 800; font-size: 28px; line-height: 1.18; }
  .services__lead { left: 36px; top: 389px; color: var(--ink); font-weight: 300; font-size: 18px; line-height: 1.2; width: 260px; }
  .service { position: absolute; width: 100px; margin-left: -50px; text-align: center; color: var(--ink); font-weight: 300; font-size: 14px; line-height: 1.15; }
  .service svg { display: block; margin: 0 auto 6px; width: 28px; height: 26px; fill: var(--navy); }
  .front__footer { left: 0; bottom: 0; width: 100%; height: 43px; color: var(--white); font-size: 14.5px; font-weight: 400; display: flex; align-items: center; padding-left: 35px; gap: 10px; white-space: nowrap; }
  .front__footer strong { font-weight: 700; font-size: 17px; margin-left: 4px; }
  .front__footer .sep { font-weight: 700; margin: 0 2px; }

  .back__brand { left: 85px; top: 22px; }
  .back__headline { left: 30px; width: 364px; top: 82px; text-align: center; color: var(--navy); font-weight: 800; font-size: 20px; line-height: 1.25; }
  .back__lead { left: 30px; width: 364px; top: 138px; text-align: center; color: var(--grey-text); font-weight: 300; font-size: 12.5px; line-height: 1.15; }

  .plan { position: absolute; width: 133px; background: var(--white); text-align: center; padding-top: 7px; box-shadow: 0 0 10px rgba(0,0,0,.12); }
  .plan__name { color: var(--navy); font-weight: 700; font-size: 12px; }
  .plan__note { color: var(--ink); font-weight: 300; font-size: 8px; margin-top: 1px; }
  .plan__rate { color: var(--navy); font-weight: 800; font-size: 21px; margin-top: 4px; line-height: 1.1; }
  .plan__basis { color: var(--ink); font-size: 6.2px; margin-top: 4px; }
  .plan__features { list-style: none; color: var(--ink); font-size: 6.2px; line-height: 17px; margin-top: 2px; }
  .plan--lease { left: 23px; top: 193px; height: 192px; }
  .plan--full { left: 164px; top: 185px; height: 229px; }
  .plan--premium { left: 306px; top: 193px; height: 155px; }

  .contact__title { left: 23px; top: 431px; color: var(--white); font-weight: 800; font-size: 21px; line-height: 1.05; }
  .contact__lines { left: 163px; top: 430px; color: var(--white); line-height: 1.15; white-space: nowrap; }
  .contact__call { font-size: 15px; font-weight: 300; }
  .contact__phone { font-size: 19px; font-weight: 700; }
  .contact__email { font-size: 14px; font-weight: 300; }
  .contact__web { left: 370px; top: 482px; color: var(--white); font-size: 11px; letter-spacing: 1px; white-space: nowrap; }
</style>
</head>
<body>

<section class="postcard postcard--front">
  <svg class="postcard__shapes" viewBox="0 0 1381 920" preserveAspectRatio="none">
    <polygon points="0,0 115,0 0,275" fill="var(--grey)"/>
    <polygon points="115,0 170,0 55,275 0,275 0,275" fill="var(--navy-deep)"/>
    <polygon points="185,0 790,0 600,447 0,447 0,370" fill="#6f7d86" role="img" aria-label="Photo of a hand holding out a house key"/>
    <polygon points="790,0 885,0 745,333 650,333" fill="var(--navy)"/>
    <polygon points="0,447 560,447 540,487 0,487" fill="var(--navy)"/>
    <polygon points="600,333 1381,333 1381,522 495,522" fill="var(--grey)"/>
    <rect x="0" y="842" width="1381" height="78" fill="var(--navy)"/>
  </svg>

  <div class="abs brand front__brand">
    <span class="brand__name">BRAMBLECREST</span>
    <span class="brand__tag">PROPERTY MANAGEMENT</span>
  </div>
  <h1 class="abs front__headline">PROPERTY MANAGEMENT<br>ACROSS LUBBOCK, TX</h1>

  <h2 class="abs services__title">DISCOVER OUR<br>SERVICES</h2>
  <p class="abs services__lead">We offer full-service property management solutions</p>

  <div class="service" style="left:366px;top:304px">
    <svg viewBox="0 0 28 26"><path d="M14 2 1 13l2 2 2-1.7V24h7v-6h4v6h7V13.3l2 1.7 2-2Z"/></svg>Property<br>Marketing</div>
  <div class="service" style="left:464px;top:304px">
    <svg viewBox="0 0 28 26"><circle cx="9" cy="7" r="5"/><circle cx="20" cy="9" r="4"/><path d="M0 24c0-6 4-9 9-9s9 3 9 9Z"/><path d="M19 24c0-4-1-6-3-8 5-2 12 0 12 8Z"/></svg>Tenant<br>Screening</div>
  <div class="service" style="left:563px;top:304px">
    <svg viewBox="0 0 28 26"><path d="M12.5 0h3v3c3 .4 5 2 5.5 4.5l-3 .8c-.4-1.6-2-2.5-4-2.5-2.2 0-3.5 1-3.5 2.3 0 3.8 11 1.5 11 8.5 0 2.8-2.4 4.7-6 5V24h-3v-2.4c-3.5-.4-5.700-2.2-6.2-5l3.1-.7c.4 2 2.2 3 4.6 3 2.5 0 4-1 4-2.5 0-4-11-1.6-11-8.5 0-2.6 2.1-4.4 5.5-4.8Z"/></svg>Rent<br>Collection</div>
  <div class="service" style="left:662px;top:304px">
    <svg viewBox="0 0 28 26"><path d="M13 1h2v3l9 2v2l3 8c0 2.5-2 4-4 4s-4-1.5-4-4l3-8-7-1.5V22h5v3H8v-3h5V6.5L6 8l3 8c0 2.5-2 4-4 4s-4-1.5-4-4l3-8V6l9-2Zm10 9-2 6h4Zm-18 0-2 6h4Z"/></svg>Legal<br>Guidance</div>

  <div class="service" style="left:366px;top:386px">
    <svg viewBox="0 0 28 26"><path d="M10 2c5-2 10 0 12 3l4 3-3 4-4-2-12 14-4-3 13-13-1-3c-2-2-4-2-5-3Z"/></svg>Maintenance</div>
  <div class="service" style="left:464px;top:382px">
    <svg viewBox="0 0 28 26"><circle cx="11" cy="10" r="7.5" fill="none" stroke="var(--navy)" stroke-width="3.5"/><path d="m16 15 3-3 8 8-3 3Z"/></svg>Property<br>Inspections</div>
  <div class="service" style="left:563px;top:382px">
    <svg viewBox="0 0 28 26"><path d="M2 2h2.5v19H26v3H2Z"/><rect x="7" y="12" width="3" height="7"/><rect x="12" y="8" width="3" height="11"/><rect x="17" y="13" width="3" height="6"/><rect x="22" y="7" width="3" height="12"/></svg>Financial<br>Reporting</div>
  <div class="service" style="left:662px;top:382px">
    <svg viewBox="0 0 28 26"><path d="M14 1 4 5v7c0 6 4 11 10 13 6-2 10-7 10-13V5Zm0 3v18c-4-2-7-5.5-7-10V7Z"/></svg>Evictions</div>

  <div class="abs front__footer">
    <span>Call Now:<strong>(806) 555-0147</strong></span>
    <span class="sep">|</span>
    <span>info@bramblecrestpm.com</span>
    <span class="sep">|</span>
    <span>www.bramblecrestpm.com</span>
  </div>
</section>

<section class="postcard postcard--back">
  <svg class="postcard__shapes" viewBox="0 0 1381 924" preserveAspectRatio="none">
    <defs>
      <linearGradient id="teamTone" x1="0" y1="0" x2="1" y2="1">
        <stop offset="0" stop-color="#0e4c88"/>
        <stop offset="1" stop-color="#2a5c93"/>
      </linearGradient>
    </defs>
    <polygon points="841,0 896,0 650,551 590,551" fill="var(--grey)"/>
    <polygon points="896,0 1084,0 861,551 700,551" fill="var(--navy)"/>
    <polygon points="0,551 861,551 1011,924 0,924" fill="url(#teamTone)" role="img" aria-label="Photo of two agents reviewing paperwork together"/>
  </svg>

  <div class="abs brand back__brand">
    <span class="brand__name">BRAMBLECREST</span>
    <span class="brand__tag">PROPERTY MANAGEMENT</span>
  </div>
  <h2 class="abs back__headline">CHOOSE THE RIGHT PROPERTY<br>MANAGEMENT SYSTEM</h2>
  <p class="abs back__lead">Maximize your financial returns with<br>support from our rental specialists</p>

  <article class="plan plan--lease">
    <h3 class="plan__name">Lease Only</h3>
    <p class="plan__note">- You Just Need Tenants -</p>
    <p class="plan__rate">9%</p>
    <p class="plan__basis">of annual lease</p>
    <ul class="plan__features">
      <li>Professional Photography</li><li>Marketing &amp; Advertising</li><li>Property Showings</li>
      <li>Tenant Screening &amp; Qualifications</li><li>Lease Execution</li><li>Move In Coordination</li>
    </ul>
  </article>
  <article class="plan plan--full">
    <h3 class="plan__name">Full Service</h3>
    <p class="plan__note">- Our Most Popular -</p>
    <p class="plan__rate">10%</p>
    <p class="plan__basis">of monthly rent</p>
    <ul class="plan__features">
      <li>Includes Leasing Service</li><li>24/7 Emergency Response</li><li>Move In &amp; Out Inspections</li>
      <li>Professional Lease Enforcement</li><li>Schedule &amp; Oversee all Repairs</li><li>Pay all Invoices</li>
      <li>Monthly &amp; Year End Statements</li><li>Annual Market Rent Analysis</li>
    </ul>
  </article>
  <article class="plan plan--premium">
    <h3 class="plan__name">Premium Service</h3>
    <p class="plan__note">- Our Premier Service -</p>
    <p class="plan__rate">12%</p>
    <p class="plan__basis">of monthly rent</p>
    <ul class="plan__features">
      <li>Includes Full Service Features</li><li>Professional Video Marketing</li>
      <li>Home Warranty Coordination</li><li>Tenant Retention Program</li>
    </ul>
  </article>

  <p class="abs contact__title">Contact<br>Our Team</p>
  <div class="abs contact__lines">
    <p class="contact__call">Call Now:</p>
    <p class="contact__phone">(806) 555-0147</p>
    <p class="contact__email">info@bramblecrestpm.com</p>
  </div>
  <p class="abs contact__web">www.bramblecrestpm.com</p>
</section>

</body>
</html>
```